Ward Compass Business Card Design*

We need a business card design for our company Ward Compass. Our company is specialized in providing online consulting services regarding medical institutions, hospitals and doctors. We work with patients worldwide looking to choose between healthcare providers. We have a website you may use as a reference, where we list doctors and clinics worldwide. So we target Medical providers as well as patients worldwide.
Target Market(s)
Medical Providers and patients around the world
Industry/Entity Type
Medical
Contact Information for Business Card
Salwa Kettani
CEO
+90 612 348 2175
info@wardcompass.example
www.wardcompass.example
14 Annakhil 7 H.R.B. Rabat, Morocco
Requirements
Must have
- Company logo/name on one full side, personal info and smaller logo and company name on the other side.
Nice to have
- Smart and elegant design

```html
<!DOCTYPE html>
<html lang="en">
<head>
<meta charset="utf-8">
<title>Ward Compass Business Card</title>
<link rel="stylesheet" href="https://fonts.googleapis.com/css2?family=Open+Sans:ital,wght@0,400;0,600;0,700;1,400;1,700&display=swap">
<style>
  :root {
    --navy: #1c3f6e;
    --slate: #7a7a7a;
    --paper: #ffffff;
    --stage: #d9dadc;
    --ink-light: #ffffff;
  }
  * { margin: 0; padding: 0; box-sizing: border-box; }
  html, body { width: 1200px; height: 768px; overflow: hidden; }
  body {
    background: var(--stage);
    font-family: "Open Sans", Arial, sans-serif;
    position: relative;
  }
  .card {
    position: absolute;
    top: 229px;
    width: 540px;
    height: 309px;
    overflow: hidden;
    box-shadow: 0 6px 18px rgba(0,0,0,0.25);
  }
  .card--back { left: 40px; background: var(--navy); }
  .card--front { left: 620px; background: var(--slate); }

  /* back side */
  .back-brand {
    position: absolute;
    left: 0; right: 0; top: 118px;
    display: flex; align-items: center; justify-content: center; gap: 12px;
    color: var(--ink-light);
    font-weight: 600;
    font-size: 26px;
    letter-spacing: 2px;
    text-transform: uppercase;
  }
  .back-brand .dot {
    width: 22px; height: 22px; border-radius: 50%;
    background: var(--ink-light);
  }
  .back-url {
    position: absolute;
    left: 0; right: 0; bottom: 48px;
    text-align: center;
    color: var(--ink-light);
    font-size: 13px;
    letter-spacing: 5px;
  }

  /* front side */
  .front-shape { position: absolute; inset: 0; }
  .holder {
    position: absolute; left: 26px; top: 24px;
    color: var(--ink-light);
  }
  .holder__name { font-weight: 700; font-style: italic; font-size: 19px; line-height: 1.1; }
  .holder__role { font-style: italic; font-size: 12px; }
  .address {
    position: absolute; left: 26px; top: 150px;
    color: var(--ink-light); font-size: 13px; line-height: 1.35;
  }
  .contacts {
    position: absolute; left: 26px; top: 200px;
    list-style: none;
    color: var(--ink-light); font-size: 13px; line-height: 1.5;
  }
  .contacts li { display: flex; align-items: center; gap: 7px; }
  .contacts svg { width: 12px; height: 12px; fill: var(--ink-light); flex: none; }
  .front-brand {
    position: absolute; left: 300px; top: 143px;
    display: flex; align-items: center; gap: 8px;
    color: var(--navy);
    font-weight: 600; font-size: 19px; letter-spacing: 1.5px;
    text-transform: uppercase;
  }
  .front-brand .dot {
    width: 16px; height: 16px; border-radius: 50%; background: var(--navy);
  }
</style>
</head>
<body>

<section class="card card--back" aria-label="Card back">
  <div class="back-brand"><span class="dot"></span>Ward Compass</div>
  <p class="back-url">www.wardcompass.example</p>
</section>

<section class="card card--front" aria-label="Card front">
  <svg class="front-shape" width="540" height="309" viewBox="0 0 540 309" aria-hidden="true">
    <circle cx="440" cy="160" r="214" fill="none" stroke="var(--navy)" stroke-width="9"/>
    <circle cx="440" cy="160" r="206" fill="var(--paper)" stroke="var(--paper)" stroke-width="2"/>
  </svg>

  <div class="holder">
    <p class="holder__name">Salwa Kettani</p>
    <p class="holder__role">CEO</p>
  </div>

  <p class="address">14 Annakhil 7 H.R.B.<br>Rabat, Morocco</p>

  <ul class="contacts">
    <li>
      <svg viewBox="0 0 24 24"><path d="M6.6 10.8a15 15 0 0 0 6.6 6.6l2.2-2.2a1 1 0 0 1 1-.25 11.4 11.4 0 0 0 3.6.57 1 1 0 0 1 1 1V20a1 1 0 0 1-1 1A17 17 0 0 1 3 4a1 1 0 0 1 1-1h3.5a1 1 0 0 1 1 1c0 1.25.2 2.45.57 3.57a1 1 0 0 1-.25 1z"/></svg>
      +90 612 348 2175
    </li>
    <li>
      <svg viewBox="0 0 24 24"><path d="M2 5h20v14H2zM4 7v.5l8 5 8-5V7l-8 5z"/></svg>
      info@wardcompass.example
    </li>
    <li>
      <svg viewBox="0 0 24 24"><circle cx="12" cy="12" r="10"/></svg>
      www.wardcompass.example
    </li>
  </ul>

  <div class="front-brand"><span class="dot"></span>Ward Compass</div>
</section>

</body>
</html>
```